Catalogue Design Project

We need a catalog design for a new private university called Redwell Institute Bayshore (see website www.rwi-bs.org). The catalog should be about 30 pages maximum and will include items such as General Information, Academic schedule, department descriptions, program descriptions, course descriptions, school policies, student services, admissions, San diego Lifestyle, etc.
I will provide the text but I need a professional design with regard to page layouts. I have provided some examples.
Ok, i posted the catalog content, just missing course descriptions.
Target Market(s)
Young Professionals, Foreign Students
Industry/Entity Type
University
Look and feel
Each slider illustrates characteristics of the customer's brand and the style your logo design should communicate.

```html
<!DOCTYPE html>
<html lang="en">
<head>
<meta charset="utf-8">
<title>Marketing Certificate – Certificate Programs</title>
<link href="https://fonts.googleapis.com/css2?family=Carlito:wght@400;700&display=swap" rel="stylesheet">
<style>
  :root {
    --ink: #1a1a1a;
    --brand-blue: #2e6aa3;
    --rule-blue: #5b87b8;
    --footer-grey: #8a8a8a;
    --paper: #ffffff;
    --mark-tone-a: #c9d6e4;
    --mark-tone-b: #e4e7eb;
    --header-warm: #e9dcc2;
    --header-soft: #f6f1e7;
  }
  html, body {
    margin: 0;
    padding: 0;
    overflow: hidden;
  }
  body {
    width: 927px;
    height: 1200px;
    background: var(--paper);
    font-family: "Carlito", "Calibri", sans-serif;
    color: var(--ink);
  }
  .page {
    position: relative;
    width: 927px;
    height: 1200px;
    overflow: hidden;
    background: var(--paper);
  }
  .brand-mark {
    position: absolute;
    left: 58px;
    top: 32px;
    width: 150px;
    height: 40px;
    border-radius: 6px;
    background: linear-gradient(90deg, var(--mark-tone-a), var(--mark-tone-b));
  }
  .header-visual {
    position: absolute;
    left: 560px;
    top: 0;
    width: 367px;
    height: 103px;
    background: linear-gradient(90deg, rgba(246,241,231,0) 0%, var(--header-soft) 30%, var(--header-warm) 100%);
  }
  .header-rule {
    position: absolute;
    left: 0;
    top: 103px;
    width: 927px;
    height: 2px;
    background: var(--rule-blue);
  }
  .section-banner {
    position: absolute;
    left: 560px;
    top: 103px;
    width: 367px;
    height: 42px;
  }
  .section-banner svg { position: absolute; inset: 0; }
  .section-banner span {
    position: absolute;
    left: 20px;
    right: 0;
    top: 4px;
    text-align: center;
    color: var(--paper);
    font-size: 30px;
    letter-spacing: 0.5px;
    line-height: 36px;
  }
  .content {
    position: absolute;
    left: 80px;
    width: 804px;
    font-size: 19px;
  }
  .program-title {
    top: 193px;
    margin: 0;
    text-align: center;
    font-size: 25px;
    font-weight: 700;
  }
  .intro {
    top: 228px;
    line-height: 37.5px;
    text-align: justify;
  }
  .intro p { margin: 0; }
  .facts {
    top: 561px;
    line-height: 26px;
  }
  .facts p, .course-group p { margin: 0; }
  .facts strong { font-weight: 700; }
  .course-group {
    line-height: 27.3px;
  }
  .course-group h2 {
    margin: 0;
    font-size: 19px;
    font-weight: 400;
    text-decoration: underline;
  }
  .course-group ul {
    list-style: none;
    margin: 0;
    padding: 0;
  }
  .required { top: 641px; }
  .electives { top: 777px; }
  .outcome { top: 990px; }
  .footer-rule {
    position: absolute;
    left: 0;
    top: 1156px;
    width: 927px;
    height: 1px;
    background: var(--rule-blue);
  }
  .folio {
    position: absolute;
    right: 36px;
    top: 1170px;
    font-size: 14px;
    color: var(--footer-grey);
    letter-spacing: 0.3px;
  }
</style>
</head>
<body>
<div class="page">
  <div class="brand-mark" role="img" aria-label="Small dotted institute emblem"></div>
  <div class="header-visual" role="img" aria-label="Photograph of an open book fading into the page"></div>
  <div class="header-rule"></div>
  <div class="section-banner">
    <svg width="367" height="42" viewBox="0 0 367 42" aria-hidden="true">
      <polygon points="14,0 367,0 367,42 0,42" fill="var(--brand-blue)"/>
    </svg>
    <span>CERTIFICATE PROGRAMS</span>
  </div>

  <h1 class="content program-title">Marketing Certificate</h1>

  <div class="content intro">
    <p>The Marketing Certificate is designed for students who are interested in studying basic as well as advanced concepts related to Marketing and want to put them to use in real-world opportunities. Students will have the opportunity to construct actual marketing plans to add to their portfolios as well as utilize for achievement of personal objectives.</p>
    <p>Specifically, students will learn to build and sustain successful, integrated interactive marketing programs that can be used for both a current company project or for one's own business. Strong class focus will be on use of digital marketing methods to generate Internet traffic, search engine optimization, search engine marketing, as well as mobile and email marketing techniques.</p>
  </div>

  <div class="content facts">
    <p><strong>Hours:</strong> 6 hours per week</p>
    <p><strong>Length:</strong> 8 weeks per course</p>
  </div>

  <section class="content course-group required">
    <h2>Required Courses:</h2>
    <ul>
      <li>BUS 601 Statistics</li>
      <li>MKT 600 Marketing Principles</li>
      <li>MKT 601 Marketing Research</li>
    </ul>
  </section>

  <section class="content course-group electives">
    <h2>Elective Courses: (Choose 2)</h2>
    <ul>
      <li>MKT 602 Internet Advertising Solutions</li>
      <li>MKT 603 Consumer Behavior</li>
      <li>MKT 604 Global Marketing</li>
      <li>MKT 605 E-commerce</li>
      <li>MKT 607 Marketing Internship</li>
      <li>BUS 600 Starting Your Own Business</li>
    </ul>
  </section>

  <section class="content course-group outcome">
    <h2>Learning Outcome:</h2>
    <p>Strong comprehension of offline and online marketing practices, knowledge of marketing plan production and implementation of tools to design and sell a product successfully.</p>
  </section>

  <div class="footer-rule"></div>
  <div class="folio">11::: REDWELL INSTITUTE</div>
</div>
</body>
</html>
```